WordPress webdesign with coding for our company BRISK The Answer

BRISK The Answer is a payrolling company such as Montaval Wages (one of our competitor https://www.montaval-wages.ch/fr/). We need to set up our website in both languages (Fr and Eng). Our logo is enclosed.
we would like something simple explaining what is payrolling in Graph and wording, who we are and a contact page. you can also take some example if needed from our mother company BRISK The Horizon (www.briskthehorizon.ch) or our sister company (www.briskyourstride.ch). we would like to keep the color panel of our logo (ref. Black = PANTONE P Process Black C
Pink = PANTONE P Process Magenta C
Grey = PANTONE 430 C) as the driver of the website.

```html
<!DOCTYPE html>
<html lang="en">
<head>
<meta charset="UTF-8">
<title>BRISK The Answer – Flexible Payrolling Solutions</title>
<link href="https://fonts.googleapis.com/css2?family=Montserrat:wght@300;400;600;700;800&family=Roboto:wght@400;500;700&family=Parisienne&display=swap" rel="stylesheet">
<style>
:root{
  --pink:#c3155f;
  --pink-dark:#a80f50;
  --ink:#1b1b1d;
  --grey:#7b8588;
  --grey-soft:#8d9598;
  --text:#5f6467;
  --line:#e3e3e3;
  --blush:#fcf1f5;
  --white:#ffffff;
}
*{margin:0;padding:0;box-sizing:border-box}
html,body{width:1200px;height:4110px;overflow:hidden;background:var(--white)}
body{position:relative;font-family:'Roboto',Arial,sans-serif;color:var(--ink)}
.abs{position:absolute}
a{color:inherit;text-decoration:none}

/* header */
.site-header{position:absolute;left:0;top:0;width:1200px;height:104px;background:var(--white);z-index:5}
.brand{left:145px;top:34px;font-family:'Montserrat',sans-serif;font-weight:800;font-size:30px;letter-spacing:1px;color:var(--ink)}
.main-nav{left:466px;top:44px;display:flex;gap:0;font-family:'Roboto',sans-serif;font-weight:500;font-size:15px}
.main-nav a{position:absolute;white-space:nowrap;color:var(--ink)}
.nav-tick{position:absolute;left:484px;top:62px}
.nav-sep{left:990px;top:38px;width:1px;height:28px;background:var(--line)}
.lang{left:1011px;top:44px;display:flex;align-items:center;gap:8px}
.lang .flag{width:22px;height:14px;background:var(--grey);border-radius:2px}

/* hero */
.hero-art{left:0;top:104px}
.hero-title{left:710px;top:200px;font-family:'Montserrat',sans-serif;font-size:50px;line-height:55px;color:var(--ink);letter-spacing:1px}
.hero-title b{font-weight:800}
.hero-title span{font-weight:300}
.hero-sub{left:710px;top:383px;width:380px;font-size:21px;line-height:32px;color:var(--ink)}
.btn{position:absolute;display:flex;align-items:center;justify-content:center;gap:10px;border-radius:30px;background:var(--pink);color:var(--white);font-family:'Roboto',sans-serif;font-weight:700;font-size:15px;letter-spacing:.3px}
.btn.grey{background:var(--grey)}
.social-rail{left:1135px;top:248px;width:1px;height:200px;background:#bfbfbf}
.social-dot{position:absolute;width:24px;height:24px;border-radius:50%;background:var(--white);border:1.5px solid var(--pink)}
.social-dot.fill{background:var(--pink)}

/* service circles */
.service{position:absolute;border-radius:50%;background:var(--white);box-shadow:0 8px 28px rgba(0,0,0,.13);text-align:center}
.service.active{border:3px solid var(--pink);box-shadow:0 10px 30px rgba(195,21,95,.28)}
.service h3{font-family:'Roboto',sans-serif;font-weight:500;font-size:23px;color:var(--ink);margin-top:12px}
.service p{font-size:15.5px;line-height:27px;color:var(--text);margin:16px auto 0;width:230px}
.service .more{display:inline-block;margin-top:16px;color:var(--pink);font-weight:700;font-size:15px;text-decoration:underline}
.service svg{display:block;margin:0 auto}

/* about */
.about-photo{left:0;top:1085px;width:640px;height:620px;background:linear-gradient(90deg,#6e7b86 0%,#9aa5ad 30%,#cfd4d8 62%,rgba(255,255,255,0) 100%)}
.script{font-family:'Parisienne',cursive;color:var(--ink)}
.section-title{font-family:'Montserrat',sans-serif;font-weight:300;color:var(--ink);letter-spacing:1.5px}
.section-title b{font-weight:800}
.about-script{left:145px;top:1118px;font-size:44px}
.about-title{left:145px;top:1183px;font-size:50px}
.about-copy{left:575px;top:1122px;width:476px;font-size:15.5px;line-height:32px;color:var(--text);text-align:justify}

/* process */
.process-bg{left:0;top:1690px}
.centered{left:0;width:1200px;text-align:center}
.step-line{left:183px;top:1900px;width:1px;height:300px;background:#c7c7c7}
.step-icon{position:absolute;width:76px;height:76px;border-radius:50%;display:flex;align-items:center;justify-content:center;background:var(--grey)}
.step-icon.on{background:var(--pink)}
.step{position:absolute;left:250px;width:300px}
.step h4{font-weight:500;font-size:19.5px;color:var(--ink)}
.step p{margin-top:16px;font-size:15.5px;line-height:29px;color:var(--text)}
.dash-shot{left:606px;top:1931px;width:530px;height:354px;border-radius:22px;background:var(--white);box-shadow:0 10px 30px rgba(0,0,0,.12);padding:22px}
.dash-shot .screen{width:100%;height:100%;border-radius:6px;background:linear-gradient(135deg,#f4dfe6 0%,#fbf3f6 50%,#ead3dc 100%)}
.dash-back{left:780px;top:1820px;width:420px;height:345px;border-radius:16px 0 0 16px;background:linear-gradient(135deg,#e9e8e8,#f6f4f4)}

/* blog */
.post{position:absolute;top:2777px;width:280px;height:315px;background:var(--white);box-shadow:0 4px 14px rgba(0,0,0,.14);text-align:center;padding-top:30px}
.post.active{border-bottom:5px solid var(--pink)}
.post .date{color:var(--pink);font-weight:500;font-size:14px;display:flex;align-items:center;justify-content:center;gap:8px}
.post h5{margin:22px auto 0;width:230px;font-weight:700;font-size:17px;line-height:25px;color:#2d2d2f}
.post p{margin:20px auto 0;width:240px;font-size:15.5px;line-height:26px;color:var(--text)}
.post .more{display:inline-block;margin-top:14px;color:var(--pink);font-weight:700;font-size:15px;text-decoration:underline}
.arrow-btn{position:absolute;width:42px;height:42px;border-radius:50%;border:1.5px solid #9a9a9a;display:flex;align-items:center;justify-content:center}

/* cta */
.cta{left:0;top:3280px;width:1200px;height:370px;background:linear-gradient(90deg,#c3155f 0%,#c81d68 55%,#a30f4e 100%)}
.cta-photo{left:0;top:3280px}
.cta-title{left:147px;top:3355px;font-family:'Montserrat',sans-serif;color:var(--white);font-size:46px;line-height:68px;letter-spacing:2px}
.cta-title span{font-weight:300}
.cta-title b{font-weight:800}

/* footer */
.foot-head{position:absolute;top:3728px;font-weight:700;font-size:19px;color:var(--ink)}
.foot-rule{position:absolute;top:3774px;width:108px;height:2px;background:#dcdcdc}
.foot-rule::before{content:"";position:absolute;left:0;top:0;width:22px;height:2px;background:var(--pink)}
.foot-div{position:absolute;top:3723px;width:1px;height:262px;background:#cfcfcf}
.foot-text{position:absolute;font-size:15.5px;line-height:27px;color:var(--ink)}
.foot-input{left:516px;top:3848px;width:252px;height:40px;border:1.5px solid #bfbfbf;border-radius:22px;font-size:13px;padding:12px 18px;color:var(--ink)}
.quick a{display:block;font-size:15.5px;line-height:33px;color:var(--ink)}
.copyright{left:140px;top:4042px;font-size:15px;color:var(--ink)}
.foot-social{position:absolute;top:4038px;width:30px;height:30px;border-radius:50%;border:1.5px solid var(--pink)}
.foot-social.fill{background:var(--pink)}
</style>
</head>
<body>

<!-- HEADER -->
<header class="site-header">
  <div class="abs brand">BRISK The Answer</div>
  <nav class="abs main-nav">
    <a href="#" style="left:0">HOME</a>
    <a href="#" style="left:87px">WHAT IS PAYROLLING</a>
    <a href="#" style="left:291px">WHO WE ARE</a>
    <a href="#" style="left:431px">CONTACT</a>
  </nav>
  <svg class="nav-tick" width="24" height="14" viewBox="0 0 24 14"><path d="M2 6l5 5L20 2" fill="none" stroke="#c3155f" stroke-width="2.5"/></svg>
  <div class="abs nav-sep"></div>
  <div class="abs lang"><span class="flag" aria-label="English"></span><svg width="10" height="6"><path d="M0 0h10L5 6z" fill="#1b1b1d"/></svg></div>
</header>

<!-- HERO -->
<svg class="abs hero-art" width="1200" height="900" viewBox="0 0 1200 900">
  <defs>
    <linearGradient id="heroGrad" x1="0" y1="0" x2="1" y2="0">
      <stop offset="0" stop-color="#c9cbcb"/>
      <stop offset=".35" stop-color="#b7bcc2"/>
      <stop offset=".6" stop-color="#dcdcd9"/>
      <stop offset="1" stop-color="#e6e5e2"/>
    </linearGradient>
  </defs>
  <polygon role="img" aria-label="Photo of a young woman in glasses reviewing a payroll document at her desk" points="0,0 1200,0 1200,446 620,620 420,700 0,440" fill="url(#heroGrad)"/>
  <polygon points="70,520 160,585 152,592 62,528" fill="#c3155f"/>
  <polygon points="700,592 790,566 792,578 704,602" fill="#c3155f"/>
</svg>

<h1 class="abs hero-title"><b>FLEXIBLE</b><br><span>PAYROLLING</span><br><b>SOLUTIONS</b></h1>
<p class="abs hero-sub">Expertise and Efficiency for All Your Payrolling Needs.</p>
<a class="btn" href="#" style="left:710px;top:478px;width:254px;height:52px">DISCOVER PAYROLLING
  <svg width="24" height="14" viewBox="0 0 24 14"><path d="M2 7l5 5L21 1" fill="none" stroke="#fff" stroke-width="2"/></svg></a>

<div class="abs social-rail"></div>
<span class="social-dot" style="left:1123px;top:296px" aria-label="Social profile"></span>
<span class="social-dot fill" style="left:1123px;top:334px" aria-label="Social profile"></span>
<span class="social-dot" style="left:1123px;top:372px" aria-label="Social profile"></span>

<!-- SERVICE CIRCLES -->
<div class="service" style="left:62px;top:675px;width:358px;height:358px;padding-top:30px">
  <svg width="56" height="56" viewBox="0 0 56 56"><circle cx="20" cy="18" r="8" fill="none" stroke="#c3155f" stroke-width="2"/><path d="M6 50c0-12 6-18 14-18s14 6 14 18" fill="none" stroke="#1b1b1d" stroke-width="2"/><rect x="32" y="6" width="18" height="24" rx="2" fill="none" stroke="#c3155f" stroke-width="2"/><circle cx="41" cy="42" r="8" fill="none" stroke="#c3155f" stroke-width="2"/></svg>
  <h3>Payrolling</h3>
  <p>Sed ut perspiciatis unde mnis iste natus error sit oluptatem accusantium udantium</p>
  <a class="more" href="#">READ MORE</a>
</div>

<div class="service active" style="left:426px;top:670px;width:354px;height:354px;padding-top:44px">
  <svg width="60" height="60" viewBox="0 0 60 60"><rect x="22" y="22" width="16" height="16" fill="none" stroke="#c3155f" stroke-width="2"/><g fill="none" stroke="#1b1b1d" stroke-width="2"><circle cx="8" cy="8" r="5"/><circle cx="52" cy="8" r="5"/><circle cx="8" cy="52" r="5"/><circle cx="52" cy="52" r="5"/><circle cx="30" cy="5" r="4"/><circle cx="30" cy="55" r="4"/><path d="M12 12l10 10M48 12L38 22M12 48l10-10M48 48L38 38M30 9v13M30 38v13"/></g></svg>
  <h3>Sourcing</h3>
  <p>Sed ut perspiciatis unde mnis iste natus error sit oluptatem accusantium udantium</p>
  <a class="more" href="#">READ MORE</a>
</div>

<div class="service" style="left:784px;top:575px;width:354px;height:354px;padding-top:62px">
  <svg width="60" height="52" viewBox="0 0 60 52"><rect x="2" y="8" width="16" height="14" fill="none" stroke="#c3155f" stroke-width="2"/><rect x="42" y="8" width="16" height="14" fill="none" stroke="#c3155f" stroke-width="2"/><rect x="22" y="2" width="16" height="10" fill="none" stroke="#c3155f" stroke-width="2"/><circle cx="30" cy="30" r="6" fill="none" stroke="#1b1b1d" stroke-width="2"/><path d="M18 50c0-8 5-12 12-12s12 4 12 12" fill="none" stroke="#1b1b1d" stroke-width="2"/></svg>
  <h3>Payroll Outsourcing</h3>
  <p>Sed ut perspiciatis unde mnis iste natus error sit oluptatem accusantium udantium</p>
  <a class="more" href="#">READ MORE</a>
</div>

<!-- ABOUT -->
<div class="abs about-photo" role="img" aria-label="Photo of hands typing on a laptop in a bright office"></div>
<div class="abs script about-script">About</div>
<h2 class="abs section-title about-title">WHO <b>WE ARE</b></h2>
<svg class="abs" style="left:147px;top:1255px" width="36" height="22" viewBox="0 0 36 22"><path d="M2 10l7 7L22 3" fill="none" stroke="#c3155f" stroke-width="2.5"/><path d="M14 17L32 2" fill="none" stroke="#c3155f" stroke-width="2"/></svg>
<p class="abs about-copy">Sed ut perspiciatis unde omnis iste natus error sit voluptatem accusantium doloremque laudantium, totam rem aperiam, eaque ipsa quae ab illo inventore veritatis et quasi architecto beatae vitae dicta sunt explicabo. Nemo enim ipsam voluptatem quia voluptas sit aspernatur aut odit aut fugit, sed quia consequuntur magni dolores eos qui ratione voluptatem sequi nesciunt. Neque porro quisquam est, qui dolorem ipsum quia dolor sit amet, consectetur, adipisci velit, sed quia non numquam eius modi tempora incidunt ut labore et dolore magnam aliquam quaerat voluptatem.</p>
<a class="btn" href="#" style="left:576px;top:1436px;width:188px;height:50px">READ MORE
  <svg width="24" height="14" viewBox="0 0 24 14"><path d="M2 7l5 5L21 1" fill="none" stroke="#fff" stroke-width="2"/></svg></a>

<!-- PROCESS -->
<svg class="abs process-bg" width="1200" height="850" viewBox="0 0 1200 850">
  <defs>
    <linearGradient id="blush" x1="0" y1="0" x2="0" y2="1">
      <stop offset="0" stop-color="#ffffff"/>
      <stop offset=".3" stop-color="#fcf2f5"/>
      <stop offset="1" stop-color="#fbf4f6"/>
    </linearGradient>
  </defs>
  <polygon points="0,0 1200,0 1200,610 340,835 0,590" fill="url(#blush)"/>
  <polygon points="70,592 340,842 720,736 340,826" fill="#c3155f"/>
</svg>

<div class="abs script centered" style="top:1630px;font-size:44px">Process</div>
<h2 class="abs section-title centered" style="top:1698px;font-size:50px">WHAT IS <b>PAYROLLING</b></h2>
<svg class="abs" style="left:582px;top:1768px" width="36" height="22" viewBox="0 0 36 22"><path d="M2 10l7 7L22 3" fill="none" stroke="#c3155f" stroke-width="2.5"/><path d="M14 17L32 2" fill="none" stroke="#c3155f" stroke-width="2"/></svg>

<div class="abs step-line"></div>
<div class="step-icon on" style="left:145px;top:1834px"><svg width="36" height="36" viewBox="0 0 36 36"><circle cx="14" cy="10" r="6" fill="none" stroke="#fff" stroke-width="2"/><path d="M3 32c0-9 5-13 11-13s11 4 11 13" fill="none" stroke="#fff" stroke-width="2"/><rect x="22" y="22" width="12" height="10" fill="none" stroke="#fff" stroke-width="2"/></svg></div>
<div class="step-icon" style="left:145px;top:2002px"><svg width="34" height="34" viewBox="0 0 34 34"><rect x="5" y="3" width="22" height="28" rx="2" fill="none" stroke="#fff" stroke-width="2"/><circle cx="18" cy="18" r="6" fill="none" stroke="#fff" stroke-width="2"/><path d="M22 22l6 6" stroke="#fff" stroke-width="2"/></svg></div>
<div class="step-icon" style="left:145px;top:2169px"><svg width="36" height="36" viewBox="0 0 36 36"><circle cx="18" cy="18" r="14" fill="none" stroke="#fff" stroke-width="2"/><circle cx="18" cy="18" r="7" fill="none" stroke="#fff" stroke-width="2"/><circle cx="18" cy="18" r="2" fill="#fff"/></svg></div>

<div class="step" style="top:1831px"><h4>We Employ</h4><p>Sed ut perspiciatis unde omnis iste natus error sit voluptatemccusantium doloremque laudantium</p></div>
<div class="step" style="top:1999px"><h4>We Manage Payroll</h4><p>Sed ut perspiciatis unde omnis iste natus error sit voluptatemccusantium doloremque laudantium</p></div>
<div class="step" style="top:2167px"><h4>You Focus on Your Business</h4><p>Sed ut perspiciatis unde omnis iste natus error sit voluptatemccusantium doloremque laudantium</p></div>

<div class="abs" style="left:575px;top:1897px;width:140px;height:140px;border-radius:50%;background:#6d7376"></div>
<div class="abs" style="left:1035px;top:2185px;width:140px;height:140px;border-radius:50%;background:var(--pink)"></div>
<div class="abs dash-back" role="img" aria-label="Secondary payroll dashboard screen"></div>
<div class="abs dash-shot"><div class="screen" role="img" aria-label="Payroll dashboard screen with charts and analytics"></div></div>

<!-- BLOG -->
<div class="abs script centered" style="top:2565px;font-size:44px">Blog</div>
<h2 class="abs section-title centered" style="top:2628px;font-size:50px">LATEST <b>POSTS</b></h2>
<svg class="abs" style="left:582px;top:2700px" width="36" height="22" viewBox="0 0 36 22"><path d="M2 10l7 7L22 3" fill="none" stroke="#c3155f" stroke-width="2.5"/><path d="M14 17L32 2" fill="none" stroke="#c3155f" stroke-width="2"/></svg>

<div class="arrow-btn" style="left:64px;top:2913px"><svg width="12" height="18"><path d="M10 2L3 9l7 7" fill="none" stroke="#888" stroke-width="2"/></svg></div>
<div class="arrow-btn" style="left:1093px;top:2913px"><svg width="12" height="18"><path d="M2 2l7 7-7 7" fill="none" stroke="#888" stroke-width="2"/></svg></div>

<article class="post" style="left:145px">
  <div class="date"><svg width="20" height="20"><circle cx="10" cy="10" r="10" fill="#c3155f"/><rect x="5" y="6" width="10" height="9" fill="none" stroke="#fff" stroke-width="1.5"/></svg>Jun 15,2025</div>
  <h5>DUIS AUTE IRURE DOLOR IEXPLICABON REPREH</h5>
  <p>Sed ut perspiciatis unde omnis iste natus error sit voluptatem accusantium doloremque ntium, totam rem aperiam</p>
  <a class="more" href="#">READ MORE</a>
</article>
<article class="post active" style="left:460px">
  <div class="date"><svg width="20" height="20"><circle cx="10" cy="10" r="10" fill="#c3155f"/><rect x="5" y="6" width="10" height="9" fill="none" stroke="#fff" stroke-width="1.5"/></svg>Jun 15,2025</div>
  <h5>DUIS AUTE IRURE DOLOR IEXPLICABON REPREH</h5>
  <p>Sed ut perspiciatis unde omnis iste natus error sit voluptatem accusantium doloremque ntium, totam rem aperiam</p>
  <a class="more" href="#">READ MORE</a>
</article>
<article class="post" style="left:775px">
  <div class="date"><svg width="20" height="20"><circle cx="10" cy="10" r="10" fill="#c3155f"/><rect x="5" y="6" width="10" height="9" fill="none" stroke="#fff" stroke-width="1.5"/></svg>Jun 15,2025</div>
  <h5>DUIS AUTE IRURE DOLOR IEXPLICABON REPREH</h5>
  <p>Sed ut perspiciatis unde omnis iste natus error sit voluptatem accusantium doloremque ntium, totam rem aperiam</p>
  <a class="more" href="#">READ MORE</a>
</article>

<a class="btn" href="#" style="left:506px;top:3146px;width:188px;height:52px">VIEW MORE
  <svg width="24" height="14" viewBox="0 0 24 14"><path d="M2 7l5 5L21 1" fill="none" stroke="#fff" stroke-width="2"/></svg></a>

<!-- CTA -->
<div class="abs cta"></div>
<svg class="abs cta-photo" width="1200" height="370" viewBox="0 0 1200 370">
  <defs>
    <linearGradient id="ctaPhoto" x1="0" y1="0" x2="1" y2="1">
      <stop offset="0" stop-color="#3f4a5a"/>
      <stop offset=".5" stop-color="#8a97a6"/>
      <stop offset="1" stop-color="#b9c0c8"/>
    </linearGradient>
  </defs>
  <polygon role="img" aria-label="Photo of a financial bar chart rising above a desk with reports" points="822,0 1200,0 1200,370 718,370" fill="url(#ctaPhoto)"/>
</svg>
<h2 class="abs cta-title"><span>SIMPLIFY YOUR HR &amp;</span><br><b>PAYROLL TODAY</b></h2>
<a class="btn grey" href="#" style="left:147px;top:3513px;width:187px;height:50px">CONTACT US
  <svg width="24" height="14" viewBox="0 0 24 14"><path d="M2 7l5 5L21 1" fill="none" stroke="#fff" stroke-width="2"/></svg></a>

<!-- FOOTER -->
<footer>
  <h6 class="foot-head" style="left:140px">CONTACT US</h6>
  <div class="foot-rule" style="left:140px"></div>
  <svg class="abs" style="left:143px;top:3806px" width="16" height="20" viewBox="0 0 16 20"><path d="M8 19S1 11 1 7a7 7 0 0114 0c0 4-7 12-7 12z" fill="#c3155f"/><circle cx="8" cy="7" r="2.5" fill="#fff"/></svg>
  <p class="foot-text" style="left:177px;top:3798px;width:200px">234,Sed ut prspiciatis unde omnis iste natt voluptate</p>
  <svg class="abs" style="left:143px;top:3872px" width="18" height="18" viewBox="0 0 18 18"><path d="M4 1l3 4-2 2c1 3 3 5 6 6l2-2 4 3-2 3C8 17 1 10 1 3z" fill="#c3155f"/></svg>
  <p class="foot-text" style="left:177px;top:3862px">Phone:<br>+1 888 888 8888</p>
  <svg class="abs" style="left:143px;top:3928px" width="18" height="14" viewBox="0 0 18 14"><rect width="18" height="14" rx="1" fill="#c3155f"/><path d="M1 1l8 6 8-6" fill="none" stroke="#fff" stroke-width="1.5"/></svg>
  <p class="foot-text" style="left:177px;top:3914px">Email:<br>info@companyname.com</p>

  <div class="foot-div" style="left:452px"></div>
  <h6 class="foot-head" style="left:515px">SIGN UP FOR NEWSLETTER</h6>
  <div class="foot-rule" style="left:515px"></div>
  <p class="foot-text" style="left:515px;top:3798px">Sed ut prspiciatis unde omnis iste</p>
  <div class="abs foot-input">Enter email</div>
  <a class="btn" href="#" style="left:516px;top:3903px;width:252px;height:40px;font-size:14px">SUBSCRIBE
    <svg width="24" height="14" viewBox="0 0 24 14"><path d="M2 7l5 5L21 1" fill="none" stroke="#fff" stroke-width="2"/></svg></a>

  <div class="foot-div" style="left:851px"></div>
  <h6 class="foot-head" style="left:922px">QUICK LINKS</h6>
  <div class="foot-rule" style="left:922px"></div>
  <nav class="abs quick" style="left:922px;top:3792px">
    <a href="#">Home</a><a href="#">What is Payrolling</a><a href="#">Who We &nbsp;Are</a><a href="#">Contact</a>
  </nav>

  <p class="abs copyright">© 2025 Companyname.All Rights Reserved | Privacy Policy &nbsp;| &nbsp;Terms of use</p>
  <span class="foot-social" style="left:944px" aria-label="Social profile"></span>
  <span class="foot-social fill" style="left:984px" aria-label="Social profile"></span>
  <span class="foot-social" style="left:1024px" aria-label="Social profile"></span>
</footer>

</body>
</html>
```